Awesome photographers card for an awesome new business

Double sided business card Black background and silver logo in middle on one side. Details on otherside. please keep it simple

Industry/Entity Type

Photographer

Contact Information for Business Card

Gerald Fenwick
0452817360
GeraldFenwickPhotography47@mailbox.test
www.GeraldFenwickPhotography.test.au
Instagram _Gerald_fenwick

Requirements
Must have
• My logo in Silver
• please use instagram logo instead of "Instagram"

```html
<!DOCTYPE html>
<html lang="en">
<head>
<meta charset="utf-8">
<title>Gerald Fenwick Photography — Business Card</title>
<link rel="stylesheet" href="https://fonts.googleapis.com/css2?family=Source+Sans+3:wght@400;600&display=swap">
<style>
  :root {
    --stage: #000000;
    --card-center: #ffffff;
    --card-mid: #dcdddf;
    --card-edge: #9a9b9e;
    --ink: #1c1c1c;
    --rule: #222222;
    --mark: #3a3a3a;
  }
  html, body {
    margin: 0;
    padding: 0;
    width: 1200px;
    height: 900px;
    overflow: hidden;
    background: var(--stage);
  }
  .canvas {
    position: relative;
    width: 1200px;
    height: 900px;
    background: var(--stage);
    font-family: "Source Sans 3", sans-serif;
  }
  .card {
    position: absolute;
    top: 275px;
    width: 477px;
    height: 293px;
    background: radial-gradient(ellipse 60% 70% at 50% 50%,
      var(--card-center) 0%, var(--card-mid) 48%, var(--card-edge) 100%);
    overflow: hidden;
  }
  .card--details {
    left: 116px;
    border-radius: 0 46px 0 46px;
  }
  .card--brand {
    left: 622px;
    top: 276px;
    height: 292px;
    border-radius: 46px 0 46px 0;
  }
  .details {
    position: absolute;
    left: 0;
    right: 0;
    top: 81px;
    text-align: center;
    color: var(--ink);
  }
  .details__name {
    margin: 0;
    font-size: 18px;
    font-weight: 600;
    line-height: 24px;
  }
  .details__rule {
    width: 139px;
    height: 2px;
    margin: 12px auto 9px;
    background: var(--rule);
    border: 0;
  }
  .details__line {
    margin: 0;
    font-size: 14px;
    line-height: 19.7px;
  }
  .brand {
    position: absolute;
    left: 143px;
    top: 48px;
    width: 190px;
    height: 190px;
    border: 3px solid var(--mark);
    border-radius: 50%;
    box-sizing: border-box;
    display: flex;
    align-items: center;
    justify-content: center;
    text-align: center;
  }
  .brand__name {
    margin: 0;
    color: var(--mark);
    font-size: 19px;
    font-weight: 600;
    line-height: 24px;
  }
</style>
</head>
<body>
  <main class="canvas">
    <section class="card card--details" aria-label="Contact side">
      <div class="details">
        <h1 class="details__name">Gerald Fenwick</h1>
        <hr class="details__rule">
        <p class="details__line">0452817360</p>
        <p class="details__line">GeraldFenwickPhotography47@mailbox.test</p>
        <p class="details__line">www.GeraldFenwickPhotography.test.au</p>
        <p class="details__line">Gerald_fenwick</p>
      </div>
    </section>
    <section class="card card--brand" aria-label="Brand side">
      <div class="brand">
        <p class="brand__name">Gerald Fenwick<br>Photography</p>
      </div>
    </section>
  </main>
</body>
</html>
```